We (R. T. Galvin & Partners, Inc.) are an executive Search firm based in Los Angeles that is exclusively focused in the Med Tech and Health Tech arenas.   I need a logo to communicate that we are a high end search firm, but also that we are focused in the medicine and science arenas called health tech and med tech.  Many of our clients have robotics and artificial intelligence type products, so it is very technology forward.  I tend to gravitate towards clean, sharp aesthetic as opposed to something that is really over the top.
Attached are files with my logo in two different layouts.  In addition to the letterhead and envelope, I also will need an electronic letterhead in Microsoft Word.  I tend to
I look forward to seeing the designs and just let me know if you have any questions.
Dale

```html
<!DOCTYPE html>
<html lang="en">
<head>
<meta charset="utf-8">
<title>R. T. Galvin &amp; Partners, Inc. — Stationery</title>
<link href="https://fonts.googleapis.com/css2?family=Montserrat:wght@400;500&display=swap" rel="stylesheet">
<style>
  :root {
    --backdrop: #d9d9d9;
    --paper: #ffffff;
    --flap: #e6e7e9;
    --ink: #111111;
    --muted: #444444;
    --brand-blue: #4a9ad8;
    --rule-blue: #6aaee0;
  }
  * { margin: 0; padding: 0; box-sizing: border-box; }
  html, body { width: 1200px; height: 859px; overflow: hidden; }
  body {
    background: var(--backdrop);
    font-family: "Montserrat", Arial, sans-serif;
    color: var(--ink);
    position: relative;
  }
  .sheet { position: absolute; background: var(--paper); }

  .wordmark { position: absolute; display: flex; align-items: center; }
  .wordmark-dot { border-radius: 50%; background: var(--brand-blue); flex: none; }
  .wordmark-text { font-weight: 500; color: var(--ink); line-height: 1; }
  .wordmark-name { display: block; letter-spacing: 0.01em; }
  .wordmark-sub { display: block; letter-spacing: 0.28em; }

  /* Letterhead */
  .letterhead { left: 61px; top: 49px; width: 583px; height: 754px; }
  .letterhead .wordmark { left: 63px; top: 52px; }
  .letterhead .wordmark-dot { width: 22px; height: 22px; margin-right: 14px; }
  .letterhead .wordmark-name { font-size: 20px; }
  .letterhead .wordmark-sub { font-size: 9px; margin-top: 6px; }
  .footer-rule { position: absolute; left: 63px; top: 671px; width: 457px; height: 1px; background: var(--rule-blue); }
  .contact-list { position: absolute; left: 63px; top: 685px; list-style: none; font-size: 9px; color: var(--muted); }
  .contact-list li { display: flex; align-items: center; height: 11.5px; }
  .contact-list svg { width: 7px; height: 7px; margin-right: 5px; fill: none; stroke: var(--brand-blue); stroke-width: 1.4; }
  .letterhead-address { position: absolute; right: 63px; top: 708px; text-align: right; font-size: 9px; line-height: 11.5px; color: var(--muted); font-style: normal; }

  /* Envelopes */
  .envelope { left: 687px; width: 452px; }
  .envelope-back-open { top: 50px; height: 279px; }
  .envelope-back-closed { top: 353px; height: 212px; }
  .envelope-front { top: 587px; height: 213px; }
  .flap { position: absolute; left: 0; top: 0; width: 100%; height: 67px; }
  .envelope .wordmark-dot { width: 11px; height: 11px; margin-right: 8px; }
  .envelope .wordmark-name { font-size: 12px; }
  .envelope .wordmark-sub { font-size: 5.5px; margin-top: 3px; }
  .envelope-back-open .wordmark { left: 168px; top: 23px; }
  .envelope-back-closed .wordmark { left: 168px; top: 23px; }
  .envelope-front .wordmark { left: 24px; top: 25px; }
  .return-address { position: absolute; left: 24px; top: 57px; font-size: 7.5px; line-height: 9px; color: var(--muted); font-style: normal; }
</style>
</head>
<body>

  <section class="sheet letterhead" aria-label="Letterhead">
    <div class="wordmark">
      <span class="wordmark-dot"></span>
      <span class="wordmark-text">
        <span class="wordmark-name">R. T. GALVIN</span>
        <span class="wordmark-sub">&amp; PARTNERS INC.</span>
      </span>
    </div>

    <div class="footer-rule"></div>

    <ul class="contact-list">
      <li><svg viewBox="0 0 10 10"><path d="M2 1 L4 1 L4.6 3.4 L3.3 4.2 Q4.3 6.2 5.8 6.7 L6.6 5.4 L9 6 L9 8 Q5 9.5 1.5 4 Q1 2 2 1 Z"/></svg>+1 (310) 555-0142</li>
      <li><svg viewBox="0 0 10 10"><rect x="1" y="4" width="8" height="4"/><rect x="3" y="1" width="4" height="3"/><rect x="3" y="7" width="4" height="2"/></svg>+1 (310) 555-0187</li>
      <li><svg viewBox="0 0 10 10"><rect x="1" y="2" width="8" height="6"/><path d="M1 2 L5 5.5 L9 2"/></svg>office@rtgalvinpartners.com</li>
      <li><svg viewBox="0 0 10 10"><circle cx="5" cy="5" r="4"/><path d="M1 5 H9 M5 1 Q2.5 5 5 9 M5 1 Q7.5 5 5 9"/></svg>www.rtgalvinpartners.com</li>
    </ul>

    <address class="letterhead-address">1840 Westmont Drive<br>Los Angeles, CA 90025</address>
  </section>

  <section class="sheet envelope envelope-back-open" aria-label="Envelope back, flap open">
    <svg class="flap" viewBox="0 0 452 67" preserveAspectRatio="none" aria-hidden="true">
      <path d="M0 67 L18 8 Q20 0 30 0 L422 0 Q432 0 434 8 L452 67 Z" fill="var(--flap)"/>
    </svg>
    <div class="wordmark">
      <span class="wordmark-dot"></span>
      <span class="wordmark-text">
        <span class="wordmark-name">R. T. GALVIN</span>
        <span class="wordmark-sub">&amp; PARTNERS INC.</span>
      </span>
    </div>
  </section>

  <section class="sheet envelope envelope-back-closed" aria-label="Envelope back, flap closed">
    <svg class="flap" viewBox="0 0 452 67" preserveAspectRatio="none" aria-hidden="true">
      <path d="M0 0 L18 58 Q21 67 31 67 L421 67 Q431 67 434 58 L452 0" fill="none" stroke="#c9c9c9" stroke-width="1"/>
    </svg>
    <div class="wordmark">
      <span class="wordmark-dot"></span>
      <span class="wordmark-text">
        <span class="wordmark-name">R. T. GALVIN</span>
        <span class="wordmark-sub">&amp; PARTNERS INC.</span>
      </span>
    </div>
  </section>

  <section class="sheet envelope envelope-front" aria-label="Envelope front">
    <div class="wordmark">
      <span class="wordmark-dot"></span>
      <span class="wordmark-text">
        <span class="wordmark-name">R. T. GALVIN</span>
        <span class="wordmark-sub">&amp; PARTNERS INC.</span>
      </span>
    </div>
    <address class="return-address">1840 Westmont Drive<br>Los Angeles, CA 90025</address>
  </section>

</body>
</html>
```